Kestrelmoor Air Business Card Design

Design new, 2 sides, business cards for a residential and light commercial heating, air conditioning contractor.

Target Market(s)

Homeowners, small businesses

Industry/Entity Type

Business

Contact Information for Business Card

Dominic Westerhall
Phone - 862-415-2736
Email
Address - PO box 518
Brightwater NJ 07912
Website - www.KestrelmoorAirLLC.example

Requirements
Must have
• logo, company colors, standard size with no die cut, so I can use nova stamp

```html
<!DOCTYPE html>
<html lang="en">
<head>
<meta charset="utf-8">
<title>Kestrelmoor Air Business Card</title>
<link rel="stylesheet" href="https://fonts.googleapis.com/css2?family=Barlow:wght@400;500;600&family=Roboto:wght@400&display=swap">
<style>
  :root {
    --page: #ececec;
    --card: #7d2a2c;
    --gold: #e2b416;
    --name-gold: #f2b22a;
    --cream: #f6e6b8;
    --light: #efe4dc;
    --ink: #2a1a10;
  }
  * { margin: 0; padding: 0; box-sizing: border-box; }
  html, body { width: 1200px; height: 576px; overflow: hidden; }
  body {
    background: var(--page);
    position: relative;
    font-family: "Barlow", sans-serif;
  }
  .card {
    position: absolute;
    top: 138px;
    background: var(--card);
    overflow: hidden;
  }
  .card--front { left: 81px; width: 485px; height: 294px; }
  .card--back { left: 602px; width: 481px; height: 292px; }

  .brand-name {
    position: absolute;
    left: 0; right: 0;
    text-align: center;
    font-family: "Barlow", sans-serif;
    font-weight: 600;
    color: var(--cream);
    letter-spacing: 1px;
    white-space: nowrap;
  }
  .card--front .brand-name { top: 110px; font-size: 40px; }
  .card--back .brand-name { top: 80px; font-size: 36px; }

  .service-band {
    position: absolute;
    left: 0; right: 0;
    top: 249px;
    height: 23px;
    background: var(--gold);
    color: var(--ink);
    font-family: "Roboto", sans-serif;
    font-size: 12.5px;
    line-height: 23px;
    text-align: center;
    white-space: nowrap;
  }
  .service-band .dot { margin: 0 4px; }

  .person { position: absolute; left: 26px; top: 198px; }
  .person-name { color: var(--name-gold); font-weight: 600; font-size: 17px; }
  .person-title { color: var(--light); font-size: 11px; margin-top: 2px; }

  .contact-list {
    position: absolute;
    left: 264px;
    top: 199px;
    list-style: none;
  }
  .contact-list li {
    display: flex;
    align-items: center;
    color: var(--light);
    font-size: 11.6px;
    height: 17px;
    white-space: nowrap;
  }
  .contact-list svg { width: 11px; height: 11px; margin-right: 12px; fill: var(--gold); flex: none; }

  .bottom-strip {
    position: absolute;
    left: 0; right: 0; bottom: 0;
    height: 7px;
    background: var(--gold);
  }
</style>
</head>
<body>
  <section class="card card--front">
    <p class="brand-name">Kestrelmoor Air</p>
    <p class="service-band">Residential &amp; Light Commercial Heating <span class="dot">•</span>Air Conditioning Contractor</p>
  </section>

  <section class="card card--back">
    <p class="brand-name">Kestrelmoor Air</p>
    <div class="person">
      <p class="person-name">Dominic Westerhall</p>
      <p class="person-title">Managing Director</p>
    </div>
    <ul class="contact-list">
      <li><svg viewBox="0 0 12 12"><path d="M1 4c0-2 2-3 5-3s5 1 5 3v1H8V4H4v1H1zM3 6h6l2 5H1z"/></svg>862-415-2736</li>
      <li><svg viewBox="0 0 12 12"><path d="M0 2h12v1L6 7 0 3zM0 4.5l6 4 6-4V10H0z"/></svg>info@KestrelmoorAirLLC.example</li>
      <li><svg viewBox="0 0 12 12"><path d="M6 0a6 6 0 100 12A6 6 0 006 0zm-1 1.2C4 2.5 3.6 4 3.5 5.4H1.3A4.8 4.8 0 015 1.2zm2 0a4.8 4.8 0 013.7 4.2H8.5C8.4 4 8 2.5 7 1.2zM4.6 5.4C4.7 4 5.2 2.6 6 1.6c.8 1 1.3 2.4 1.4 3.8zm-3.3 1.2h2.2c.1 1.4.5 2.9 1.5 4.2a4.8 4.8 0 01-3.7-4.2zm3.3 0h2.8c-.1 1.4-.6 2.8-1.4 3.8-.8-1-1.3-2.4-1.4-3.8zm3.9 0h2.2A4.8 4.8 0 017 10.8c1-1.3 1.4-2.8 1.5-4.2z"/></svg>www.KestrelmoorAirLLC.example</li>
      <li><svg viewBox="0 0 12 12"><path d="M6 0a4 4 0 00-4 4c0 3 4 8 4 8s4-5 4-8a4 4 0 00-4-4zm0 5.6A1.6 1.6 0 116 2.4a1.6 1.6 0 010 3.2z"/></svg>PO box 518 Brightwater NJ 07912</li>
    </ul>
    <div class="bottom-strip"></div>
  </section>
</body>
</html>
```